RB Halden Electric Yard Sign

Looking to have a yard sign designed that we can place at projects we are working on. Most likely will be 18" H x 24" W but flexible that we can increase the size if necessary. It should include our logo, our phone # 609-555-0147, website rbhaldenelectric.example and slogan, built on integrity, driven by excellence. Colors should match our brand.

```html
<!DOCTYPE html>
<html lang="en">
<head>
<meta charset="utf-8">
<title>RB Halden Electric Yard Sign</title>
<link rel="stylesheet" href="https://fonts.googleapis.com/css2?family=Montserrat:wght@400;500;700&display=swap">
<style>
  :root {
    --sign-white: #ffffff;
    --brand-navy: #1c3764;
    --ink: #0d0d0d;
  }
  * { margin: 0; padding: 0; box-sizing: border-box; }
  html, body {
    width: 1200px;
    height: 846px;
    overflow: hidden;
    background: var(--sign-white);
  }
  .yard-sign {
    width: 1200px;
    height: 846px;
    position: relative;
    font-family: "Montserrat", Arial, sans-serif;
    color: var(--ink);
    text-align: center;
  }
  .brand-name {
    position: absolute;
    left: 0;
    right: 0;
    top: 180px;
    font-weight: 700;
    font-size: 84px;
    letter-spacing: 2px;
    line-height: 1;
    color: var(--brand-navy);
    text-transform: uppercase;
    white-space: nowrap;
  }
  .phone {
    position: absolute;
    left: 0;
    right: 0;
    top: 432px;
    font-weight: 500;
    font-size: 138px;
    line-height: 1;
    letter-spacing: 1px;
    white-space: nowrap;
  }
  .website {
    position: absolute;
    left: 0;
    right: 0;
    top: 604px;
    font-weight: 400;
    font-size: 60px;
    line-height: 1;
    white-space: nowrap;
  }
  .slogan {
    position: absolute;
    left: 0;
    right: 0;
    top: 730px;
    font-weight: 400;
    font-size: 55px;
    line-height: 1;
    white-space: nowrap;
  }
</style>
</head>
<body>
  <main class="yard-sign">
    <h1 class="brand-name">RB Halden Electric</h1>
    <p class="phone">609-555-0147</p>
    <p class="website">rbhaldenelectric.example</p>
    <p class="slogan">Built on integrity, driven by excellence</p>
  </main>
</body>
</html>
```